Business cards - BRENT Roofing & Siding

We need simple business cards made up for our Roofing & Siding business based in Calgary Alberta.
The logo on one side of the card and potentially our slogan "Built with trust, verified by time".
The other side could have:
-A small logo
-Rep name:
-Rep cell phone:
-Rep email:
-Office phone: 403-684-2093
-Website: PrairieShingleWorks.com

We would like to incorporate the colours from our logo, especially the lite blue on the jpeg file. I have attached the ai file and jpeg file. We like the colours better on the jpeg file.

I do not require a money back guarantee

```html
<!DOCTYPE html>
<html lang="en">
<head>
<meta charset="utf-8">
<title>BRENT Roofing &amp; Siding – Business Cards</title>
<link href="https://fonts.googleapis.com/css2?family=Montserrat:wght@400;500;600;700&display=swap" rel="stylesheet">
<style>
  :root {
    --stage: #e6e7e9;
    --card: #1c1c1d;
    --blue: #1a8cf0;
    --blue-deep: #1570c8;
    --white: #ffffff;
    --muted: #d9dde2;
  }
  * { margin: 0; padding: 0; box-sizing: border-box; }
  html, body { width: 1200px; height: 852px; overflow: hidden; }
  body {
    background: var(--stage);
    font-family: "Montserrat", sans-serif;
    position: relative;
  }
  .card {
    position: absolute;
    width: 540px;
    height: 310px;
    background: var(--card);
    border-radius: 16px;
    overflow: hidden;
    box-shadow: 0 10px 30px rgba(0,0,0,0.25);
  }
  .card--front { left: 40px; top: 271px; }
  .card--back  { left: 620px; top: 271px; }

  .brand {
    position: absolute;
    color: var(--white);
    font-weight: 600;
    text-align: center;
  }
  .brand__row { display: flex; align-items: center; justify-content: center; gap: 12px; }
  .brand__mark { width: 18px; height: 18px; background: var(--blue); }
  .brand__name { letter-spacing: 4px; line-height: 1; }
  .brand__trade { letter-spacing: 3px; margin-top: 8px; }
  .brand__est { font-weight: 500; letter-spacing: 1px; margin-bottom: 8px; color: var(--white); }

  .card--front .brand { left: 0; right: 0; top: 92px; }
  .card--front .brand__name { font-size: 64px; }
  .card--front .brand__trade { font-size: 18px; }
  .card--front .brand__est { font-size: 12px; }

  .card--back .brand { left: 34px; top: 34px; text-align: left; }
  .card--back .brand__row { justify-content: flex-start; gap: 8px; }
  .card--back .brand__mark { width: 12px; height: 12px; }
  .card--back .brand__name { font-size: 40px; letter-spacing: 3px; }
  .card--back .brand__trade { font-size: 11.5px; letter-spacing: 2px; margin-top: 6px; }
  .card--back .brand__est { font-size: 9px; margin-bottom: 6px; }

  .rep {
    position: absolute;
    right: 40px;
    top: 108px;
    text-align: right;
  }
  .rep__name { color: var(--blue); font-weight: 700; font-size: 22px; letter-spacing: 0.5px; }
  .rep__title { color: var(--white); font-weight: 500; font-size: 13px; letter-spacing: 1px; margin-top: 2px; }

  .divider {
    position: absolute;
    left: 96px;
    right: 26px;
    top: 178px;
    height: 1.5px;
    background: var(--blue-deep);
  }
  .tab {
    position: absolute;
    right: -14px;
    top: 86px;
    width: 28px;
    height: 40px;
    border-radius: 14px;
    background: var(--blue);
  }

  .contacts {
    position: absolute;
    left: 96px;
    top: 196px;
    list-style: none;
    color: var(--white);
    font-size: 15px;
    font-weight: 500;
  }
  .contacts li { display: flex; align-items: center; gap: 10px; line-height: 25px; }
  .contacts svg { width: 12px; height: 12px; flex: none; }
</style>
</head>
<body>

  <section class="card card--front" aria-label="Business card front">
    <div class="brand">
      <div class="brand__est">Est. 1991</div>
      <div class="brand__row">
        <span class="brand__mark"></span>
        <span class="brand__name">BRENT</span>
      </div>
      <div class="brand__trade">ROOFING &amp; SIDING</div>
    </div>
  </section>

  <section class="card card--back" aria-label="Business card back">
    <div class="brand">
      <div class="brand__est">Est. 1991</div>
      <div class="brand__row">
        <span class="brand__mark"></span>
        <span class="brand__name">BRENT</span>
      </div>
      <div class="brand__trade">ROOFING &amp; SIDING</div>
    </div>

    <span class="tab"></span>

    <div class="rep">
      <div class="rep__name">DANIEL HARGROVE</div>
      <div class="rep__title">DIRECTOR</div>
    </div>

    <div class="divider"></div>

    <ul class="contacts">
      <li>
        <svg viewBox="0 0 12 12" aria-hidden="true"><path d="M2.5 1 L4.5 1 L5.2 3.6 L4 4.6 C4.7 6 6 7.3 7.4 8 L8.4 6.8 L11 7.5 L11 9.5 C11 10.3 10.3 11 9.5 11 C5 11 1 7 1 2.5 C1 1.7 1.7 1 2.5 1 Z" fill="#1a8cf0"/></svg>
        403-684-2093
      </li>
      <li>
        <svg viewBox="0 0 12 12" aria-hidden="true"><rect x="3" y="0.8" width="6" height="10.4" rx="1.2" fill="none" stroke="#1a8cf0" stroke-width="1.3"/><circle cx="6" cy="9.3" r="0.7" fill="#1a8cf0"/></svg>
        905-318-4470
      </li>
      <li>
        <svg viewBox="0 0 12 12" aria-hidden="true"><rect x="0.8" y="2.2" width="10.4" height="7.6" rx="1" fill="none" stroke="#1a8cf0" stroke-width="1.2"/><path d="M1 2.6 L6 6.6 L11 2.6" fill="none" stroke="#1a8cf0" stroke-width="1.2"/></svg>
        brentroof@prairiemail.net
      </li>
      <li>
        <svg viewBox="0 0 12 12" aria-hidden="true"><circle cx="6" cy="6" r="5" fill="none" stroke="#1a8cf0" stroke-width="1.1"/><ellipse cx="6" cy="6" rx="2.2" ry="5" fill="none" stroke="#1a8cf0" stroke-width="1"/><path d="M1 6 H11 M2 3.5 H10 M2 8.5 H10" stroke="#1a8cf0" stroke-width="0.9"/></svg>
        PrairieShingleWorks.com
      </li>
    </ul>
  </section>

</body>
</html>
```